I am looking to create a newly designed website for our national leadership conference which is entitled, "The Harbor of Momentum Leadership Summit". The Harbor of Momentum Leadership Summit is a national conference for student leaders that prepares them for career leadership success. The current website can be seen at www.harborofmomentumleadershipsummit.com.

My goal for the new site is to create a more updated, fresh, hip, and exciting look that appeals to the younger generation while also maintaining are professional appeal. The color should be black, white, and gold. We want there to be live videos played and places to insert pictures for the panels as well.

I look forward to seeing you the new creations.

Requirements
Must have
• Ability to play videos on the home page and throughout the website. Also, make sure that the website shows up clearly on an zTablet.
Nice to have
• Nice look

```html
<!DOCTYPE html>
<html lang="en">
<head>
<meta charset="utf-8">
<title>Harbor of Momentum Leadership Summit</title>
<link href="https://fonts.googleapis.com/css2?family=Roboto:wght@300;400;500;700&display=swap" rel="stylesheet">
<style>
:root{
  --gold:#c4943f;
  --gold-light:#dcb56a;
  --gold-dark:#b7852f;
  --ink:#2b2b2b;
  --text:#666;
  --muted:#999;
  --line:#d9d9d9;
  --panel:#eeeeee;
  --white:#fff;
  --footer:#3a3a3a;
  --photo-dark:#4a4a4a;
  --photo-mid:#8a8a8a;
}
*{box-sizing:border-box;margin:0;padding:0}
html,body{width:685px;height:1200px;overflow:hidden;background:var(--white)}
body{font-family:'Roboto',Arial,sans-serif;color:var(--text);position:relative}
.wrap{width:534px;margin:0 auto;position:relative}

/* header */
.site-header{height:84px}
.brand{position:absolute;left:0;top:54px;display:flex;align-items:center;gap:6px}
.brand-dot{width:16px;height:16px;border-radius:50%;background:var(--gold)}
.brand-name{font-weight:700;font-size:11.5px;letter-spacing:1px;color:var(--ink)}
.social{position:absolute;left:316px;top:13px;display:flex;gap:3px}
.social span{width:19px;height:19px;background:#9a9a9a}
.social span:first-child{background:#5a6fae}
.search{position:absolute;right:0;top:13px;width:96px;height:20px;border:1px solid var(--line);font-size:6px;color:var(--muted);padding:6px 7px}
.search svg{position:absolute;right:6px;top:5px}
.nav{position:absolute;right:0;top:60px;display:flex;gap:15px;font-size:6.4px;color:#444;letter-spacing:.2px}
.nav .active{color:var(--gold)}

/* hero */
.hero{height:210px;position:relative;background:linear-gradient(160deg,#6d6d6d,#3c3c3c 55%,#555)}
.play{position:absolute;width:28px;height:20px;border-radius:5px;background:#222;display:flex;align-items:center;justify-content:center}
.play::after{content:"";border-left:8px solid #fff;border-top:5px solid transparent;border-bottom:5px solid transparent;margin-left:2px}
.play.sm{width:17px;height:12px;border-radius:3px}
.play.sm::after{border-left-width:5px;border-top-width:3px;border-bottom-width:3px}
.hero .play{left:323px;top:92px}
.arrow{position:absolute;top:96px;width:14px;height:18px;background:rgba(0,0,0,.35);display:flex;align-items:center;justify-content:center}
.arrow.left{left:0}.arrow.right{right:0}

/* register band */
.register-band{height:56px;background:linear-gradient(#d9b46a,var(--gold) 50%,#b98a3a)}
.register-band .wrap{display:flex;align-items:center;height:56px;gap:16px}
.btn-dark{background:var(--ink);color:#fff;font-size:8.5px;padding:7px 10px;border-radius:2px;white-space:nowrap}
.register-band p{font-size:6.4px;color:#2a2a2a;line-height:1.65}

/* welcome */
.welcome{height:156px;text-align:center;padding-top:32px}
.section-title{color:var(--gold);font-weight:700;font-size:19px;letter-spacing:.5px}
.welcome p{font-size:5.8px;line-height:1.9;text-transform:uppercase;margin-top:8px;color:#777}
.btn-outline{display:inline-block;margin-top:12px;border:1px solid var(--line);font-size:5.5px;color:var(--muted);padding:7px 10px}

/* testimonials */
.testimonials{height:136px;background:var(--panel)}
.testimonials .wrap{display:flex;height:136px}
.media{position:relative;background:linear-gradient(150deg,var(--photo-mid),var(--photo-dark))}
.testimonials .media{width:242px;height:136px}
.media .play{left:50%;top:50%;transform:translate(-50%,-50%)}
.quote{padding:22px 0 0 26px;width:292px}
.quote h3{color:var(--gold);font-weight:400;font-size:13px}
.quote p{font-size:6.6px;line-height:1.75;margin-top:8px}
.quote .who{font-size:7.6px;color:var(--ink);margin-top:6px}
.dots{display:flex;gap:6px;margin-top:17px}
.dots span{width:6px;height:6px;border-radius:50%;background:#bbb}
.dots span.on{background:var(--gold)}

/* partners */
.partners{height:215px}
.partner-row{display:flex;padding-top:44px;padding-bottom:15px;border-bottom:1px solid var(--line)}
.partner-group{width:267px;text-align:center}
.partner-group+.partner-group{border-left:1px solid var(--line)}
.partner-group h4{font-size:6.6px;font-weight:400;color:var(--ink);letter-spacing:.2px}
.logos{display:flex;justify-content:space-around;align-items:center;margin-top:12px;height:30px}
.logos .name{font-size:7.4px;font-weight:500;color:var(--ink)}
.seal{width:24px;height:24px;border-radius:50%;background:#b7a07a}
.award{text-align:center;padding-top:21px}
.award h4{font-size:6.6px;font-weight:400;color:var(--ink)}
.award .name{font-size:8px;font-weight:500;color:var(--ink);margin-top:10px}

/* moments */
.moments{height:195px;background:var(--panel);text-align:center;padding-top:25px}
.moments h2{color:var(--gold);font-weight:400;font-size:12.5px}
.clips{display:flex;justify-content:space-between;margin-top:14px}
.clips .media{width:162px;height:91px}
.moments .dots{justify-content:center;margin-top:24px}

/* contact */
.contact{height:93px;text-align:center;padding-top:23px}
.contact h2{color:var(--gold);font-weight:400;font-size:12.5px}
.form{display:flex;gap:11px;margin-top:15px;align-items:center}
.field{height:18px;border:1px solid var(--line);font-size:5.4px;color:var(--muted);text-align:left;padding:6px 6px}
.send{background:#555;color:#fff;font-size:5.4px;padding:6px 7px}

/* footer */
.site-footer{height:55px;background:var(--footer)}
.site-footer .wrap{height:55px}
.foot-brand{position:absolute;left:0;top:24px;display:flex;align-items:center;gap:5px}
.foot-brand .brand-dot{width:10px;height:10px;background:#888}
.foot-brand span{font-size:6px;font-weight:700;letter-spacing:.8px;color:#aaa}
.foot-nav{position:absolute;right:0;top:18px;font-size:5.6px;color:#ccc;letter-spacing:.2px}
.copyright{position:absolute;right:0;top:32px;font-size:5.6px;color:#bbb}
</style>
</head>
<body>

<header class="site-header">
  <div class="wrap">
    <div class="brand"><span class="brand-dot"></span><span class="brand-name">HARBOR OF MOMENTUM</span></div>
    <div class="social"><span></span><span></span><span></span><span></span><span></span></div>
    <div class="search">Search
      <svg width="8" height="8" viewBox="0 0 10 10"><circle cx="4" cy="4" r="3" fill="none" stroke="#777" stroke-width="1.3"/><line x1="6.3" y1="6.3" x2="9" y2="9" stroke="#777" stroke-width="1.3"/></svg>
    </div>
    <nav class="nav">
      <span class="active">HOME</span><span>ABOUT</span><span>CONFERENCE</span><span>REGISTER</span><span>TESTIMONIALS</span><span>Y FACTOR</span><span>VIDEOS</span><span>CONTACT</span>
    </nav>
  </div>
</header>

<section class="hero" role="img" aria-label="Black and white video still of a speaker engaging students at the leadership summit">
  <div class="arrow left"><svg width="6" height="10"><polyline points="5,1 1,5 5,9" fill="none" stroke="#ddd"/></svg></div>
  <div class="play"></div>
  <div class="arrow right"><svg width="6" height="10"><polyline points="1,1 5,5 1,9" fill="none" stroke="#ddd"/></svg></div>
</section>

<section class="register-band">
  <div class="wrap">
    <span class="btn-dark">Register Now</span>
    <p>for a transformational leadership experience that will connect you with an incredible diverse leadership network of students and professionals that provide you with the inspiration and leadership/professional skills needed to take your life to the next level!</p>
  </div>
</section>

<section class="welcome">
  <div class="wrap">
    <h1 class="section-title">WELCOME</h1>
    <p>The Harbor of Momentum Leadership Experience is a three day conference that not only connects student leaders nationally with an incredible diverse leadership network of students and professionals that will provide them with the inspiration, leadership development training, and professional skills needed to take their personal and leadership experience to the next level, but it's a life changing conference that consists of...</p>
    <span class="btn-outline">Know more</span>
  </div>
</section>

<section class="testimonials">
  <div class="wrap">
    <div class="media" role="img" aria-label="Video still of a student sharing her summit experience among peers"><div class="play sm"></div></div>
    <div class="quote">
      <h3>Testimonials</h3>
      <p>The conference this past weekend was just too short! I had an amazing time meeting, networking, laughing and learning from such a colorful group of individuals! I absolutely cannot wait to share my experience and promote HOM 2012!</p>
      <div class="who">Marisol, Northbrook State University, Eastfield</div>
      <div class="dots"><span class="on"></span><span></span><span></span><span></span></div>
    </div>
  </div>
</section>

<section class="partners">
  <div class="wrap">
    <div class="partner-row">
      <div class="partner-group">
        <h4>NETWORK WITH EXECUTIVES</h4>
        <div class="logos"><span class="name">Fizzwell</span><span class="name">Civic Bridge</span><span class="name">Summit Academy</span><span class="name">LeeMarsh.com</span></div>
      </div>
      <div class="partner-group">
        <h4>CONNECT WITH OTHER STUDENT LEADERS FROM</h4>
        <div class="logos"><span class="seal"></span><span class="seal"></span><span class="name">Quillan State</span><span class="name">Vantmere</span><span class="name">Norhaven</span></div>
      </div>
    </div>
    <div class="award">
      <h4>VOTED AS TOP STUDENT LEADERSHIP PROGRAM OF THE YEAR IN 2014</h4>
      <div class="name">Campus Leaders Guild</div>
    </div>
  </div>
</section>

<section class="moments">
  <div class="wrap">
    <h2>EXPERIENCE TRANSFORMATIONAL MOMENTS LIKE THESE STUDENT LEADERS</h2>
    <div class="clips">
      <div class="media" role="img" aria-label="Video still of two student leaders speaking on stage"><div class="play sm"></div></div>
      <div class="media" role="img" aria-label="Video still of a student leader giving a talk"><div class="play sm"></div></div>
      <div class="media" role="img" aria-label="Video still of a student leader sharing her story"><div class="play sm"></div></div>
    </div>
    <div class="dots"><span class="on"></span><span></span><span></span><span></span></div>
  </div>
</section>

<section class="contact">
  <div class="wrap">
    <h2>Contact us</h2>
    <div class="form">
      <div class="field" style="width:89px">Name</div>
      <div class="field" style="width:101px">School/Company</div>
      <div class="field" style="width:89px">Email</div>
      <div class="field" style="width:205px">Message</div>
      <span class="send">SEND</span>
    </div>
  </div>
</section>

<footer class="site-footer">
  <div class="wrap">
    <div class="foot-brand"><span class="brand-dot"></span><span>HARBOR OF MOMENTUM</span></div>
    <div class="foot-nav">HOME &nbsp;|&nbsp; ABOUT &nbsp;|&nbsp; CONFERENCE &nbsp;|&nbsp; REGISTER &nbsp;|&nbsp; TESTIMONIALS &nbsp;|&nbsp; Y FACTOR &nbsp;|&nbsp; VIDEOS &nbsp;|&nbsp; CONTACT</div>
    <div class="copyright">Copyright © 2015 &nbsp;The Harbor of Momentum Leadership Summit. &nbsp;All rights reserved.</div>
  </div>
</footer>

</body>
</html>
```